Property Services Company Needs a Brochure Design

Looking for a new brochure design for an existing property services company.

We provide a range of property services from, market research, real estate brokerage, valuation and appraisal, property development and other real estate consulting services.

We would like a fresh modern brochure design with good graphics and features. Our colours are white, blue and orange.

The design should communicate, attention to detail, superior service delivery and distinction in results.
Updates

I would like the brochure to be roughly about 20 pages.

Containing the following,

1) An introduction
2) Contents Page
2) What we do
3) Our Services
4) Agency & Brokerage
5) Real Estate Consulting
6) Market Research
7) Appraisal & Valuation
8) Project Management
9) Property Development

I would also like icons to represent items 4,5,6,7,8 & 9, they should be represented vertically on each of the pages from the contents page and highlighted individually on the pages that they represent.. i.e. on appraisal & valuation page, all six icons will be arranged vertically and the appraisal and valuations icon will be highlighted.

I will also like to have images that depict the services on the various pages.

I have some pages I think will flow which I will upload shortly.

Industry/Entity Type

Real Estate

Font styles to use
Serif

Colors
f78f20
0455a3

```html
<!DOCTYPE html>
<html lang="en">
<head>
<meta charset="utf-8">
<title>Property Services Brochure – Pages 7–10</title>
<link href="https://fonts.googleapis.com/css2?family=Open+Sans:ital,wght@0,300;0,400;1,700&display=swap" rel="stylesheet">
<style>
  :root {
    --orange: #f78f20;
    --orange-deep: #d86c0c;
    --blue: #0455a3;
    --blue-deep: #0a2f66;
    --paper: #ffffff;
    --paper-shade: #dcdcdc;
    --ink: #3a3a3a;
    --stage: #2b2b2b;
  }
  * { margin: 0; padding: 0; box-sizing: border-box; }
  html, body { width: 1200px; height: 900px; overflow: hidden; }
  body {
    background: var(--stage);
    font-family: "Open Sans", Arial, sans-serif;
    position: relative;
  }
  .page-label {
    position: absolute;
    left: 0; width: 1200px;
    text-align: center;
    color: #fff;
    font-style: italic;
    font-weight: 700;
    font-size: 20px;
  }
  .spread {
    position: absolute;
    left: 113px;
    width: 1010px;
    height: 356px;
    overflow: hidden;
  }
  .spread-art { position: absolute; inset: 0; }
  .section-title {
    position: absolute;
    top: 16px;
    color: #fff;
    font-weight: 300;
    font-size: 17px;
    letter-spacing: 0.3px;
    text-align: center;
    width: 300px;
  }
  .body-copy {
    position: absolute;
    color: var(--ink);
    font-size: 10px;
    white-space: nowrap;
  }
  .body-copy.left { left: 50px; top: 148px; line-height: 18.7px; }
  .body-copy.right { right: 13px; top: 149px; line-height: 17px; text-align: right; }
</style>
</head>
<body>

<div class="page-label" style="top:56px;">page 7-8</div>

<section class="spread" style="top:88px;">
  <svg class="spread-art" viewBox="0 0 1010 356" width="1010" height="356">
    <defs>
      <linearGradient id="paperA" x1="0" y1="0" x2="1" y2="1">
        <stop offset="0" stop-color="var(--paper-shade)"/>
        <stop offset="0.45" stop-color="var(--paper)"/>
        <stop offset="1" stop-color="var(--paper-shade)"/>
      </linearGradient>
      <linearGradient id="bandA" x1="0" y1="0" x2="1" y2="0">
        <stop offset="0" stop-color="var(--orange-deep)"/>
        <stop offset="1" stop-color="var(--orange)"/>
      </linearGradient>
      <linearGradient id="blueA" x1="0" y1="0" x2="1" y2="1">
        <stop offset="0" stop-color="var(--blue)"/>
        <stop offset="1" stop-color="var(--blue-deep)"/>
      </linearGradient>
      <linearGradient id="officeA" x1="0" y1="0" x2="0" y2="1">
        <stop offset="0" stop-color="#e4e6e8"/>
        <stop offset="0.6" stop-color="#b9bdc0"/>
        <stop offset="1" stop-color="#6d7276"/>
      </linearGradient>
    </defs>
    <rect class="paper" x="0" y="0" width="1010" height="356" fill="url(#paperA)"/>
    <rect class="edge-strip" x="0" y="0" width="27" height="356" fill="url(#blueA)"/>
    <rect class="header-band" x="27" y="0" width="479" height="52" fill="url(#bandA)"/>
    <rect class="icon-box" x="42" y="0" width="102" height="134" fill="var(--orange-deep)"/>
    <g class="icon-growth" fill="#f1f1f1">
      <rect x="55" y="84" width="14" height="28"/>
      <rect x="75" y="72" width="14" height="40"/>
      <rect x="95" y="62" width="14" height="50"/>
      <rect x="115" y="54" width="14" height="58"/>
      <polyline points="54,74 78,50 92,60 122,28" fill="none" stroke="#f1f1f1" stroke-width="5"/>
      <polygon points="112,22 132,18 128,38"/>
    </g>
    <polygon class="blue-field" points="506,0 542,0 917,356 347,356 506,196" fill="url(#blueA)"/>
    <polygon class="photo" role="img" aria-label="Photo of a modern office with glass desk and mesh chair" points="622,77 785,240 785,356 506,356 506,193" fill="url(#officeA)"/>
    <polygon class="header-band" points="542,0 1010,0 1010,52 597,52" fill="url(#bandA)"/>
    <line x1="542" y1="0" x2="917" y2="356" stroke="var(--orange)" stroke-width="7"/>
    <line x1="622" y1="77" x2="347" y2="356" stroke="var(--orange)" stroke-width="7"/>
    <rect class="icon-box" x="895" y="0" width="100" height="134" fill="var(--orange-deep)"/>
    <g class="icon-consult" fill="none" stroke="#f1f1f1" stroke-width="6">
      <circle cx="936" cy="58" r="22"/>
      <line x1="952" y1="74" x2="972" y2="94" stroke-width="9"/>
      <polygon points="936,44 950,58 946,58 946,70 926,70 926,58 922,58" fill="#f1f1f1" stroke="none"/>
    </g>
  </svg>
  <h2 class="section-title" style="left:202px;">AGENCY &amp; BROKERAGE</h2>
  <h2 class="section-title" style="left:589px;">REAL ESTATE CONSULTING</h2>
  <p class="body-copy left">The brokerage team, covers both landlords and tenants across the residential and<br>commercial markets. With a large database of industry specific individuals and corporate<br>twinned with a large database of inventory, we are able to very quickly understand<br>the needs of our clients and find the perfect fit. We enjoy long standing<br>relationships with many of our clients and landlords, and are always happy to<br>meet with new clients to advise on how best to maximize their rental<br>return or budget.</p>
  <p class="body-copy right">We provide a broad range of consulting services, we<br>understand that out client needs may vary and our<br>experienced team are at hand to provide tailored<br>solutions to their needs. Our professional<br>services include corporate planning,<br>feasibility studies, market studies, due<br>diligence, property tax, litigation,<br>asset review and framework for<br>foreign direct investment.</p>
</section>

<div class="page-label" style="top:468px;">page&nbsp; 9-10</div>

<section class="spread" style="top:502px;">
  <svg class="spread-art" viewBox="0 0 1010 356" width="1010" height="356">
    <defs>
      <linearGradient id="paperB" x1="0" y1="0" x2="1" y2="1">
        <stop offset="0" stop-color="var(--paper-shade)"/>
        <stop offset="0.45" stop-color="var(--paper)"/>
        <stop offset="1" stop-color="var(--paper-shade)"/>
      </linearGradient>
      <linearGradient id="bandB" x1="0" y1="0" x2="1" y2="0">
        <stop offset="0" stop-color="var(--orange-deep)"/>
        <stop offset="1" stop-color="var(--orange)"/>
      </linearGradient>
      <linearGradient id="blueB" x1="0" y1="0" x2="1" y2="1">
        <stop offset="0" stop-color="var(--blue)"/>
        <stop offset="1" stop-color="var(--blue-deep)"/>
      </linearGradient>
      <linearGradient id="lobbyB" x1="0" y1="0" x2="0" y2="1">
        <stop offset="0" stop-color="#e9e4da"/>
        <stop offset="0.55" stop-color="#9c8f7c"/>
        <stop offset="1" stop-color="#5d5448"/>
      </linearGradient>
    </defs>
    <rect x="0" y="0" width="1010" height="356" fill="url(#paperB)"/>
    <rect class="edge-strip" x="0" y="0" width="27" height="356" fill="url(#blueB)"/>
    <rect class="header-band" x="27" y="0" width="479" height="52" fill="url(#bandB)"/>
    <rect class="icon-box" x="40" y="0" width="102" height="134" fill="var(--orange-deep)"/>
    <g class="icon-research" fill="#f1f1f1">
      <circle cx="91" cy="58" r="15" fill="none" stroke="#f1f1f1" stroke-width="5"/>
      <circle cx="91" cy="53" r="5"/>
      <rect x="84" y="60" width="14" height="8" rx="4"/>
      <line x1="102" y1="69" x2="118" y2="85" stroke="#f1f1f1" stroke-width="7"/>
      <circle cx="71" cy="30" r="6"/><rect x="63" y="37" width="16" height="14" rx="3"/>
      <circle cx="111" cy="30" r="6"/><rect x="103" y="37" width="16" height="14" rx="3"/>
      <circle cx="60" cy="66" r="6"/><rect x="52" y="73" width="16" height="34" rx="3"/>
      <circle cx="124" cy="66" r="6"/><rect x="116" y="90" width="16" height="17" rx="3"/>
      <rect x="82" y="80" width="18" height="27" rx="3"/>
    </g>
    <polygon class="blue-field" points="506,0 542,0 917,356 347,356 506,196" fill="url(#blueB)"/>
    <polygon class="photo" role="img" aria-label="Photo of a bright marble office lobby with reception desk" points="622,77 785,240 785,356 506,356 506,193" fill="url(#lobbyB)"/>
    <polygon class="header-band" points="542,0 1010,0 1010,52 597,52" fill="url(#bandB)"/>
    <line x1="542" y1="0" x2="917" y2="356" stroke="var(--orange)" stroke-width="7"/>
    <line x1="622" y1="77" x2="347" y2="356" stroke="var(--orange)" stroke-width="7"/>
    <rect class="icon-box" x="895" y="0" width="100" height="134" fill="var(--orange-deep)"/>
    <g class="icon-scales" fill="#f1f1f1" stroke="#f1f1f1">
      <rect x="941" y="28" width="4" height="76" stroke="none"/>
      <rect x="925" y="102" width="36" height="5" stroke="none"/>
      <line x1="912" y1="36" x2="974" y2="36" stroke-width="3"/>
      <circle cx="943" cy="30" r="4" stroke="none"/>
      <line x1="914" y1="36" x2="902" y2="70" stroke-width="1.5"/>
      <line x1="914" y1="36" x2="926" y2="70" stroke-width="1.5"/>
      <line x1="972" y1="36" x2="960" y2="70" stroke-width="1.5"/>
      <line x1="972" y1="36" x2="984" y2="70" stroke-width="1.5"/>
      <path d="M900 70 H928 A14 9 0 0 1 900 70 Z" stroke="none"/>
      <path d="M958 70 H986 A14 9 0 0 1 958 70 Z" stroke="none"/>
    </g>
  </svg>
  <h2 class="section-title" style="left:184px;">MARKET RESEARCH</h2>
  <h2 class="section-title" style="left:576px;">APPRAISAL &amp; VALUATION</h2>
  <p class="body-copy left" style="left:48px;">Our market research team, regularly conduct surveys across a wide range of areas in both<br>the commercial and residential markets. They regularly produce market reports that can be<br>used for a wide range of purposes. This information also provides our team members with<br>superior knowledge of market trends, price shifts, occupancy rates and other unique<br>trends. The information provided allows us to provide information useful for<br>forecasting growth and trends in the market.</p>
  <p class="body-copy right">We provide valuation and appraisal services to clients<br>across a broad spectrum. Our valuation advice can<br>provide information to assist with portfolio<br>valuation, single asset valuation, financial<br>reporting valuation. These services are<br>provided to individuals, financial<br>institutions and corporates.<br>Appraisal methods will vary<br>based on the specific needs<br>of our clients</p>
</section>

</body>
</html>
```